Kelmo website design on shopify

Job Description:
As a web designer for Kelmo, you will be the driving force behind designing and developing our new e-commerce website. Your responsibility will be to create an attractive, functional, and intuitive online shopping experience where customers can effortlessly discover and purchase high-quality supplements such as pre-workout, creatine, and protein shakes. Your design will play a crucial role in enhancing our brand and engaging our target audience.

```html
<!DOCTYPE html>
<html lang="en">
<head>
<meta charset="utf-8">
<title>Kelmo — Supplements Store</title>
<link href="https://fonts.googleapis.com/css2?family=Montserrat:wght@400;500;600;700&display=swap" rel="stylesheet">
<style>
:root{
  --purple:#7c2d8f;
  --purple-deep:#5b1f6f;
  --lavender:#c596d0;
  --lavender-soft:#f5e8f7;
  --topbar:#ecd4ef;
  --ink:#111111;
  --muted:#6b6b6b;
  --card-shadow:0 2px 10px rgba(0,0,0,.12);
}
*{margin:0;padding:0;box-sizing:border-box}
html,body{width:1200px;height:3447px;overflow:hidden;background:#fff}
body{font-family:'Montserrat',sans-serif;color:var(--ink);position:relative}
.abs{position:absolute}

.topbar{left:0;top:0;width:1200px;height:44px;background:var(--topbar);font-size:14px;font-weight:500;display:flex;align-items:center;justify-content:center;color:#333}
.search-icon{left:116px;top:76px}
.brand{left:0;width:1200px;top:62px;display:flex;justify-content:center;align-items:center;gap:10px}
.brand-dot{width:26px;height:26px;border-radius:50%;background:var(--purple)}
.brand-name{font-size:42px;font-weight:500;color:var(--purple);letter-spacing:1px}
.cart-icon{left:1060px;top:74px}
.nav{left:0;width:1200px;top:136px;display:flex;justify-content:center;gap:20px;font-size:15px;font-weight:500}

.hero-photo{left:498px;top:190px;width:594px;height:557px;border-radius:12px;background:linear-gradient(135deg,#e9e6e2,#f6f4f1 45%,#d9d4cd)}
.hero-card{left:115px;top:256px;width:452px;height:425px;background:linear-gradient(160deg,#c390cf,#dcb6e3 55%,#f7ebf9)}
.hero-title{left:145px;top:314px;font-size:45px;font-weight:700;line-height:61px}
.hero-text{left:145px;top:458px;width:320px;font-size:14px;line-height:26px;color:#4a3552}
.btn{left:146px;top:559px;width:130px;height:43px;border-radius:4px;background:var(--purple-deep);color:#fff;font-size:15px;font-weight:700;display:flex;align-items:center;justify-content:center}

.section-title{left:99px;top:844px;font-size:34px;font-weight:600}
.pcard{top:923px;width:237px;height:320px;background:#fff;box-shadow:var(--card-shadow)}
.pimg{position:absolute;left:14px;top:14px;right:14px;height:200px;background:radial-gradient(circle at 50% 45%,#3a3a3e,#1b1b1d 55%,#f2f2f2 56%)}
.sale{position:absolute;left:12px;top:177px;padding:2px 12px;border-radius:14px;background:var(--purple-deep);color:#fff;font-size:16px}
.pname{position:absolute;left:0;right:0;top:233px;text-align:center;font-size:19px;font-weight:600}
.price{position:absolute;left:0;right:0;top:271px;text-align:center;font-size:18px}
.price s{margin-right:18px}

.quote-band{left:0;top:1338px;width:1200px;height:388px;background:linear-gradient(100deg,#b883c4,#cfa5d8 50%,#f2e1f5)}
.quote{left:150px;width:900px;top:1431px;text-align:center;font-size:28px;font-weight:500;line-height:36px}
.author{left:0;width:1200px;top:1566px;text-align:center;font-size:20px;font-weight:600}
.role{left:0;width:1200px;top:1605px;text-align:center;font-size:20px}

.fcard{background:#fff;box-shadow:var(--card-shadow)}
.fimg{position:absolute;background:radial-gradient(circle at 50% 45%,#2f2f33,#18181a 55%,#f3f3f3 57%)}
.fname{position:absolute;left:0;right:0;text-align:center;font-size:19px;font-weight:600}
.fprice{position:absolute;left:0;right:0;text-align:center;font-size:19px}
.fprice s{margin-right:16px}

.feature{top:2605px;width:240px;text-align:center}
.feature svg{display:block;margin:0 auto}
.feature h3{margin-top:18px;font-size:19px;font-weight:700}
.feature p{margin-top:14px;font-size:14px;line-height:26px;color:var(--muted)}

.footer{left:0;top:2909px;width:1200px;height:538px;background:linear-gradient(160deg,#c28fcd,#dcb9e3 50%,#f8eefa)}
.offer-title{left:0;width:1200px;top:2990px;text-align:center;font-size:32px;font-weight:600}
.offer-sub{left:0;width:1200px;top:3045px;text-align:center;font-size:14px;color:#5a4a60}
.email{left:355px;top:3085px;width:485px;height:43px;border:1px solid #8a6a93;border-radius:5px;display:flex;align-items:center;justify-content:space-between;padding:0 12px;font-size:13px;background:rgba(255,255,255,.15)}
.fcol h4{font-size:23px;font-weight:700;margin-bottom:12px}
.fcol li{list-style:none;font-size:14px;line-height:28px}
.divider{left:115px;top:3386px;width:977px;height:1px;background:#7a5c80}
.copy{left:0;width:1200px;top:3406px;text-align:center;font-size:13px}
.code{left:1134px;top:3406px;font-size:13px}
</style>
</head>
<body>

<div class="abs topbar">Save 15% on orders over $50 &nbsp;|&nbsp; Use code 15OFF at checkout</div>

<svg class="abs search-icon" width="22" height="22" viewBox="0 0 22 22" aria-label="Search"><circle cx="9" cy="9" r="6.5" fill="none" stroke="#111" stroke-width="2"/><line x1="14" y1="14" x2="20" y2="20" stroke="#111" stroke-width="2.2"/></svg>
<div class="abs brand"><span class="brand-dot"></span><span class="brand-name">Kelmo</span></div>
<svg class="abs cart-icon" width="26" height="26" viewBox="0 0 26 26" aria-label="Cart"><path d="M8 9 V7 a5 5 0 0 1 10 0 V9" fill="none" stroke="#111" stroke-width="2"/><rect x="3" y="9" width="20" height="14" rx="3" fill="#111"/><rect x="3" y="14" width="20" height="2" fill="#fff"/></svg>

<nav class="abs nav"><span>Home</span><span>About Us</span><span>Products</span><span>Blogs</span><span>Offers</span><span>Contacts</span></nav>

<div class="abs hero-photo" role="img" aria-label="Photo of a man drinking a shake from a shaker bottle, with a supplement tub on the table"></div>
<div class="abs hero-card"></div>
<h1 class="abs hero-title">Welcome To<br>Kelmo</h1>
<p class="abs hero-text">Lorem Ipsum is simply dummy text of the printing and typesetting industry. Lorem Ipsum has been the industry's standard</p>
<div class="abs btn">Shop Now</div>

<h2 class="abs section-title">Shop our most trusted formulas</h2>

<div class="abs pcard" style="left:94px">
  <div class="pimg" role="img" aria-label="Protein shake tub"></div>
  <span class="sale">Sale</span>
  <div class="pname">Protein Shakes</div>
  <div class="price"><s>$19 CAD</s>$16 CAD</div>
</div>
<div class="abs pcard" style="left:354px">
  <div class="pimg" role="img" aria-label="Creatine tub"></div>
  <div class="pname">Creatine</div>
  <div class="price">$28.00 CAD</div>
</div>
<div class="abs pcard" style="left:614px">
  <div class="pimg" role="img" aria-label="Pre-workout BCAA tub and pouch"></div>
  <div class="pname">Pre-Workout</div>
  <div class="price">$28.00 CAD</div>
</div>
<div class="abs pcard" style="left:876px">
  <div class="pimg" role="img" aria-label="Mass gainer tubs with dumbbells"></div>
  <span class="sale">Sale</span>
  <div class="pname">Mass Gainer</div>
  <div class="price">$28.00 CAD</div>
</div>

<div class="abs quote-band" role="img" aria-label="Faded photo of supplement tubs behind the testimonial"></div>
<p class="abs quote">Lorem Ipsum is simply dummy text of the printing and typesetting industry. Lorem Ipsum has been the industry's standard dummy text ever since the 1500s,</p>
<div class="abs author">John Doe</div>
<div class="abs role">Founder</div>

<div class="abs fcard" style="left:108px;top:1814px;width:459px;height:336px">
  <div class="fimg" role="img" aria-label="Protein shake tub" style="left:120px;top:30px;width:220px;height:170px"></div>
  <span class="sale" style="top:184px">Sale</span>
  <div class="fname" style="top:260px">Protein Shakes</div>
  <div class="fprice" style="top:294px"><s>$19 CAD</s>$16 CAD</div>
</div>
<div class="abs fcard" style="left:108px;top:2176px;width:459px;height:335px">
  <div class="fimg" role="img" aria-label="Creatine tub" style="left:120px;top:14px;width:220px;height:180px"></div>
  <div class="fname" style="top:260px">Creatine</div>
  <div class="fprice" style="top:294px"><s>$19 CAD</s>$16 CAD</div>
</div>
<div class="abs fcard" style="left:614px;top:1814px;width:478px;height:697px">
  <div class="fimg" role="img" aria-label="Pre-workout BCAA tub and pouch" style="left:30px;top:90px;width:418px;height:440px"></div>
  <div class="fname" style="top:620px">Pre-Workout</div>
  <div class="fprice" style="top:654px">$16 CAD</div>
</div>

<div class="abs feature" style="left:103px">
  <svg width="80" height="80" viewBox="0 0 80 80" aria-hidden="true"><path d="M40 70 C10 50 8 30 22 22 C30 18 37 22 40 28 C43 22 50 18 58 22 C72 30 70 50 40 70Z" fill="#111"/></svg>
  <h3>Lorem Ipsum</h3>
  <p>Lorem Ipsum is simply dummy text of the printing and typesetting industry.</p>
</div>
<div class="abs feature" style="left:352px">
  <svg width="80" height="80" viewBox="0 0 80 80" aria-hidden="true"><circle cx="40" cy="40" r="32" fill="none" stroke="#111" stroke-width="6"/><path d="M25 41 L36 52 L57 30" fill="none" stroke="#111" stroke-width="6"/></svg>
  <h3>Lorem Ipsum</h3>
  <p>Lorem Ipsum is simply dummy text of the printing and typesetting industry.</p>
</div>
<div class="abs feature" style="left:601px">
  <svg width="80" height="80" viewBox="0 0 80 80" aria-hidden="true"><rect x="34" y="4" width="12" height="6" fill="#111"/><circle cx="40" cy="44" r="30" fill="none" stroke="#111" stroke-width="5"/><path d="M18 44 H30 L35 34 L42 54 L47 44 H62" fill="none" stroke="#111" stroke-width="3"/></svg>
  <h3>Lorem Ipsum</h3>
  <p>Lorem Ipsum is simply dummy text of the printing and typesetting industry.</p>
</div>
<div class="abs feature" style="left:849px">
  <svg width="80" height="80" viewBox="0 0 80 80" aria-hidden="true"><path d="M40 64 C14 46 10 28 22 20 C30 15 37 19 40 25 C43 19 50 15 58 20 C70 28 66 46 40 64Z" fill="none" stroke="#111" stroke-width="5"/><path d="M18 38 H30 L35 30 L42 46 L46 38 H62" fill="none" stroke="#111" stroke-width="3"/><rect x="16" y="66" width="48" height="5" fill="#111"/></svg>
  <h3>Lorem Ipsum</h3>
  <p>Lorem Ipsum is simply dummy text of the printing and typesetting industry.</p>
</div>

<div class="abs footer"></div>
<h2 class="abs offer-title">Get 20% off your first order</h2>
<p class="abs offer-sub">Join our email list for exclusive offers and the latest news.</p>
<div class="abs email"><span>Email</span><svg width="22" height="10" viewBox="0 0 22 10" aria-hidden="true"><line x1="0" y1="5" x2="20" y2="5" stroke="#111" stroke-width="1.4"/><path d="M16 1 L21 5 L16 9" fill="none" stroke="#111" stroke-width="1.4"/></svg></div>

<div class="abs fcol" style="left:119px;top:3158px">
  <h4>Menu</h4>
  <ul><li>Home</li><li>About Us</li><li>Products</li><li>Blogs</li><li>Offers</li><li>Contacts</li></ul>
</div>
<div class="abs fcol" style="left:360px;top:3158px">
  <h4>Our Store</h4>
  <ul>
    <li><svg width="10" height="13" viewBox="0 0 10 13" aria-hidden="true"><path d="M5 13 C1 8 0 6 0 5 a5 5 0 0 1 10 0 C10 6 9 8 5 13Z" fill="#111"/><circle cx="5" cy="5" r="2" fill="#e6cde9"/></svg> 500, Kelmo Lorem Ipsum</li>
    <li>is simply dummy text of</li><li>Mon - Fri 9 a.m. - 7 p.m.</li><li>Sat - Sun 10a.m. - 6p.m.</li>
  </ul>
</div>
<div class="abs fcol" style="left:848px;top:3158px">
  <h4>Our Promise</h4>
  <ul><li>Lorem Ipsum is simply</li><li>dummy text of the</li><li>printing and typesetting</li><li>industry. Lorem Ipsum has</li></ul>
</div>
<div class="abs divider"></div>
<div class="abs copy">2023 ©Kelmo. All Rights Reserved</div>
<div class="abs code">C60</div>

</body>
</html>
```